Quiet Harbor Prints gallery website

I need a Website for a gallery with a shopify integration or maybe even better also compatible with squarespace.
the website should have following riders: Künstler, Veranstaltungen, Shop, About Us.
some nice examples for inspiration of the website architecture are:
https://www.lindwerkraum.com/
https://www.plattenbau-salon.com/de/
https://moorlichtraum.de/
It should be easy for us to make adaptations and fill the website with new content.
Attached there is the CI an logo for the brand.
Target Market(s)
Art Collectors,
Industry/Entity Type
artgallery
Coding
Coded - Design and coding required
Number of Pages Required
3 page
Font styles to use
Look and feel

```html
<!DOCTYPE html>
<html lang="en">
<head>
<meta charset="utf-8">
<title>Quiet Harbor Prints – Home</title>
<link rel="stylesheet" href="https://fonts.googleapis.com/css2?family=Belleza&family=DM+Sans:wght@400;500;600&display=block">
<style>
  :root {
    --brand-red: #c3252f;
    --ink: #1c1c1c;
    --muted: #5b5b5b;
    --soft: #7a7a7a;
    --header-bg: #f6f9fc;
    --page-bg: #ffffff;
    --rule: #e4e4e4;
    --hero-top: #eeeeee;
    --hero-bottom: #e2e2e2;
    --display: "Belleza", "Helvetica Neue", Arial, sans-serif;
    --body: "DM Sans", Arial, sans-serif;
  }
  * { box-sizing: border-box; margin: 0; padding: 0; }
  html, body { width: 867px; height: 1200px; overflow: hidden; background: var(--page-bg); }
  body { position: relative; font-family: var(--display); color: var(--ink); }
  .abs { position: absolute; }
  .display { font-family: var(--display); font-weight: 400; }

  /* Header */
  .site-header { left: 0; top: 0; width: 867px; height: 90px; background: var(--header-bg); }
  .brand-name { font-family: var(--display); font-weight: 400; color: var(--ink); white-space: nowrap; }
  .header-brand { left: 24px; top: 49px; font-size: 11px; letter-spacing: 0.2px; }
  .main-nav { top: 42px; font-family: var(--display); font-size: 14px; }
  .main-nav a { position: absolute; color: var(--ink); text-decoration: none; white-space: nowrap; }
  .main-nav a.is-active { color: var(--brand-red); }
  .account { left: 757px; top: 42px; font-family: var(--display); font-size: 14px; display: flex; align-items: center; gap: 7px; }

  /* Hero */
  .hero { left: 0; top: 90px; width: 867px; height: 388px; background: linear-gradient(180deg, var(--hero-top), #f4f4f4 55%, var(--hero-bottom)); }
  .hero-title { left: 0; top: 213px; width: 867px; text-align: center; font-size: 38px; line-height: 35px; letter-spacing: -0.6px; }
  .hero-lead { left: 0; top: 310px; width: 867px; text-align: center; font-family: var(--body); font-size: 10.6px; line-height: 14px; color: var(--muted); }
  .btn { display: flex; align-items: center; justify-content: center; gap: 24px; background: var(--brand-red); color: #fff; font-family: var(--body); font-weight: 600; font-size: 10.5px; letter-spacing: 0.3px; text-decoration: none; }
  .hero-btn { left: 371px; top: 361px; width: 124px; height: 30px; }

  /* Spotlight */
  .spotlight-image { left: 438px; top: 495px; width: 429px; height: 349px; background: linear-gradient(135deg, #2fb6c4 0%, #e8432f 35%, #1a1a1a 55%, #f2c02a 75%, #35c7d6 100%); }
  .spotlight-title { left: 70px; top: 594px; width: 300px; font-size: 27px; line-height: 31px; letter-spacing: -0.5px; }
  .spotlight-text { left: 70px; top: 667px; width: 292px; font-family: var(--body); font-size: 11.2px; line-height: 14px; color: var(--muted); }
  .spotlight-btn { left: 70px; top: 741px; width: 124px; height: 30px; }

  /* Subscribe */
  .subscribe-title { left: 0; top: 908px; width: 867px; text-align: center; font-size: 27px; letter-spacing: -0.4px; }
  .subscribe-lead { left: 0; top: 952px; width: 867px; text-align: center; font-family: var(--display); font-size: 9.5px; color: var(--muted); }
  .email-field { left: 324px; top: 986px; width: 154px; height: 21px; border: 1px solid #d6d6d6; border-radius: 2px; font-family: var(--display); font-size: 7px; color: #777; display: flex; align-items: center; justify-content: space-between; padding: 0 7px; }
  .subscribe-btn { left: 487px; top: 986px; width: 56px; height: 21px; background: var(--brand-red); color: #fff; font-family: var(--display); font-size: 7.5px; display: flex; align-items: center; justify-content: center; }
  .subscribe-note { left: 0; top: 1024px; width: 867px; text-align: center; font-family: var(--display); font-size: 7.5px; }

  /* Footer */
  .footer-rule { left: 0; top: 1078px; width: 867px; height: 1px; background: var(--rule); }
  .footer-links { top: 1096px; font-family: var(--display); font-size: 9.5px; line-height: 16.3px; list-style: none; }
  .footer-brand { left: 360px; top: 1146px; width: 147px; text-align: center; font-size: 12.5px; }
  .social { left: 676px; top: 1096px; display: flex; gap: 9px; }
  .social span { width: 8px; height: 8px; border-radius: 50%; background: var(--ink); }
  .lang { left: 670px; top: 1157px; font-family: var(--display); font-size: 9.5px; color: var(--soft); }
</style>
</head>
<body>
  <header class="abs site-header">
    <div class="abs brand-name header-brand">QUIET HARBOR PRINTS</div>
    <nav class="abs main-nav">
      <a href="#" class="is-active" style="left:302px">Home</a>
      <a href="#" style="left:368px">Events</a>
      <a href="#" style="left:437px">Gallery</a>
      <a href="#" style="left:507px">Shop</a>
      <a href="#" style="left:567px">Contact</a>
    </nav>
    <div class="abs account">
      <svg width="11" height="11" viewBox="0 0 11 11" aria-hidden="true"><circle cx="4.3" cy="4.3" r="3.3" fill="none" stroke="#1c1c1c" stroke-width="1.2"/><line x1="6.8" y1="6.8" x2="10.2" y2="10.2" stroke="#1c1c1c" stroke-width="1.3"/></svg>
      <span>Sign in</span>
    </div>
  </header>

  <section class="abs hero" role="img" aria-label="Bright white gallery hall with framed artworks on the walls"></section>
  <h1 class="abs display hero-title">Discover Quiet Harbor Masterpieces at<br>Quiet Harbor Prints Gallery</h1>
  <p class="abs hero-lead">Embark on a journey through timeless beauty and artistic excellence at Quiet Harbor<br>Prints Gallery. Explore our curated collection of exquisite masterpieces.</p>
  <a href="#" class="abs btn hero-btn">SHOP
    <svg width="28" height="8" viewBox="0 0 28 8" aria-hidden="true"><line x1="0" y1="4" x2="27" y2="4" stroke="#fff" stroke-width="1"/><polyline points="23,1 27,4 23,7" fill="none" stroke="#fff" stroke-width="1"/></svg>
  </a>

  <div class="abs spotlight-image" role="img" aria-label="Artist painting a canvas in front of a colourful graffiti wall"></div>
  <h2 class="abs display spotlight-title">Artist Spotlight: Delving into the Creative Journey</h2>
  <p class="abs spotlight-text">Dive into the captivating narratives and creative inspirations behind our featured artists. Learn about their unique styles, passions, and contributions to the world of fine art.</p>
  <a href="#" class="abs btn spotlight-btn">ARTIST
    <svg width="28" height="8" viewBox="0 0 28 8" aria-hidden="true"><line x1="0" y1="4" x2="27" y2="4" stroke="#fff" stroke-width="1"/><polyline points="23,1 27,4 23,7" fill="none" stroke="#fff" stroke-width="1"/></svg>
  </a>

  <h2 class="abs display subscribe-title">Subscribe Now</h2>
  <p class="abs subscribe-lead">Nowadays, it isn't uncommon to see artists rapidly</p>
  <div class="abs email-field"><span>Enter your email</span>
    <svg width="8" height="6" viewBox="0 0 8 6" aria-hidden="true"><rect width="8" height="6" rx="0.8" fill="#1c1c1c"/><polyline points="0.5,0.8 4,3.4 7.5,0.8" fill="none" stroke="#fff" stroke-width="0.7"/></svg>
  </div>
  <div class="abs subscribe-btn">Subscribe</div>
  <p class="abs subscribe-note">We will never spam to you. Only useful info</p>

  <div class="abs footer-rule"></div>
  <ul class="abs footer-links" style="left:117px">
    <li>useful links</li><li>shop</li><li>affiliates</li><li>returns</li>
  </ul>
  <ul class="abs footer-links" style="left:224px">
    <li>Conditions</li><li>Privacy Policy</li><li>About Us</li><li>Contact</li>
  </ul>
  <div class="abs brand-name footer-brand">QUIET HARBOR PRINTS</div>
  <div class="abs social" aria-label="Social links"><span></span><span></span><span></span><span></span></div>
  <div class="abs lang">English/ German</div>
</body>
</html>
```